Brightfen Business Card Redesign & Logo Update

We need to update our business cards to something more modern and fresh. Brightfen can provide the current color schemes and old design examples, but welcome creativity in helping us with this redesign. PLEASE NOTE that we no longer utilize the "tree" and/or "leaf" imagery in our branding. If able would apprecaite an update on the quality of our "words only" logo in Ai. / PNG formats too.

Target Market(s)

Investors, landowners, corporate partners, contractors

Industry/Entity Type

Environmental Restoration & Conservation

Contact Information for Business Card

Logo, persons name, title, mailing address, phone and email, website url

Font styles to use
Other font styles liked:
• Merriweather

Requirements
Nice to have
• Logo, persons name, title, mailing address, phone and email, website url, but open to ideams
Should not have
• No all back backgrounds

```html
<!DOCTYPE html>
<html lang="en">
<head>
<meta charset="utf-8">
<title>Brightfen Business Card</title>
<link href="https://fonts.googleapis.com/css2?family=Merriweather:wght@400;700;900&display=swap" rel="stylesheet">
<style>
  :root {
    --backdrop: #a4a4a4;
    --card: #ffffff;
    --orange: #ee7f22;
    --green: #1a7a3e;
    --ink: #1b1b1b;
  }
  * { margin: 0; padding: 0; box-sizing: border-box; }
  html, body {
    width: 1146px;
    height: 1200px;
    overflow: hidden;
    background: var(--backdrop);
    font-family: "Merriweather", Georgia, serif;
    color: var(--ink);
  }
  .card {
    position: absolute;
    left: 175px;
    width: 797px;
    background: var(--card);
    overflow: hidden;
  }
  .card-front { top: 113px; height: 455px; }
  .card-back { top: 595px; height: 467px; }

  .wordmark {
    font-family: "Merriweather", Georgia, serif;
    font-weight: 900;
    color: var(--green);
    text-transform: uppercase;
    line-height: 1;
    white-space: nowrap;
  }
  .descriptor {
    font-weight: 700;
    text-transform: uppercase;
    color: var(--ink);
    white-space: nowrap;
    letter-spacing: 0.02em;
  }

  .front-brand {
    position: absolute;
    left: 0; right: 0;
    top: 185px;
    text-align: center;
  }
  .front-brand .wordmark { font-size: 64px; }
  .front-brand .descriptor { font-size: 16px; margin-top: 12px; }

  .back-brand {
    position: absolute;
    left: 76px;
    top: 165px;
    width: 290px;
    text-align: center;
  }
  .back-brand .wordmark { font-size: 50px; }
  .back-brand .descriptor { font-size: 12.5px; margin-top: 10px; }

  .divider {
    position: absolute;
    left: 389px;
    top: 93px;
    width: 2px;
    height: 248px;
    background: var(--orange);
  }

  .contact {
    position: absolute;
    left: 418px;
    top: 86px;
    font-size: 21px;
    line-height: 28px;
  }
  .person-name {
    font-size: 26px;
    font-weight: 900;
    line-height: 32px;
    text-transform: uppercase;
  }
  .person-name .first { color: var(--orange); }
  .person-name .last { color: var(--green); }
  .person-title { margin-bottom: 24px; }
  .address { margin-bottom: 28px; }
  .contact-line {
    display: flex;
    align-items: center;
    gap: 8px;
  }
  .contact-line svg { width: 15px; height: 15px; flex: none; }

  .wave {
    position: absolute;
    left: 0; bottom: 0;
    width: 797px;
    height: 467px;
    pointer-events: none;
  }
</style>
</head>
<body>

<section class="card card-front">
  <div class="front-brand">
    <div class="wordmark">Brightfen</div>
    <div class="descriptor">Environmental Credit Company</div>
  </div>
</section>

<section class="card card-back">
  <div class="back-brand">
    <div class="wordmark">Brightfen</div>
    <div class="descriptor">Environmental Credit Company</div>
  </div>

  <div class="divider"></div>

  <div class="contact">
    <div class="person-name"><span class="first">Marcus</span> <span class="last">Hale</span></div>
    <div class="person-title">Founder</div>
    <div class="address">
      <div>Your Company Address</div>
      <div>Fen Road 48, PO 2710, OR</div>
    </div>
    <div class="contact-line">
      <svg viewBox="0 0 16 16" aria-hidden="true"><path fill="var(--orange)" d="M3 2h3l1.5 3.5-2 1.3a8 8 0 0 0 3.7 3.7l1.3-2L14 10v3a1 1 0 0 1-1 1A11 11 0 0 1 2 3a1 1 0 0 1 1-1z"/></svg>
      <span>(555) 214-3080</span>
    </div>
    <div class="contact-line">
      <svg viewBox="0 0 16 16" aria-hidden="true"><rect x="1" y="3" width="14" height="10" fill="var(--orange)"/><path d="M1 3l7 6 7-6" fill="none" stroke="#fff" stroke-width="1.4"/></svg>
      <span>hello@brightfenmail.com</span>
    </div>
    <div class="contact-line">
      <svg viewBox="0 0 16 16" aria-hidden="true"><circle cx="8" cy="8" r="7" fill="var(--orange)"/><path d="M1 8h14M8 1c3 3 3 11 0 14M8 1c-3 3-3 11 0 14" fill="none" stroke="#fff" stroke-width="1.1"/></svg>
      <span>www.brightfenrestore.com</span>
    </div>
  </div>

  <svg class="wave" viewBox="0 0 797 467" aria-hidden="true">
    <path fill="var(--green)" d="M0 370 C120 395 250 425 420 422 C560 420 690 400 797 398 L797 467 L0 467 Z"/>
    <path fill="var(--orange)" d="M40 381 C180 412 330 420 470 408 C580 398 680 392 765 400 C680 396 580 404 470 416 C320 430 170 420 40 381 Z"/>
  </svg>
</section>

</body>
</html>
```